Sci Fi/ Secret Agent Author needs website design!

My name is Lark Whitby and I am an author. I require a site that can provide information about myself and my books and other works.

I would like it to have a Home, blog function, (about the) books/series section so people can visit another section and read about each individual book that's going to be released. A resources page, a Store, social media links and ability to load/embed videos from clipvane and other.

I write mild scifi/thriller/conspiracy/secret government type novels. -At the moment-. The series follows a strong female lead that is an agent with a secret organisation in a classified military installation.

The theme would be professional yet possibly show this element.

/military fiction/thriller/fantasy/Sci fi/ femme-fatal, readers. Mostly females, age 18-60
Novel readers

5+ page

• Would like designers to follow brief. :)
• My budget includes all the pages I will need;
• eg home, blog, resources, store, ability to pay with coinpouch and Credit Cards
• , ability to have trailers from clipvane etc. Must have links to the social media mentioned in the brief.
• use of the colours I have suggested. electric/indigo purple, fuschia highlights , dark greys
• as I will possibly base branding for social media ETC on the look of your website design and colour scheme.
• Ability for trailer on front page??
• Should not be too cluttered. (But I am open to all ideas)

```html
<!DOCTYPE html>
<html lang="en">
<head>
<meta charset="utf-8">
<title>Lark Whitby – Author</title>
<link rel="stylesheet" href="https://fonts.googleapis.com/css2?family=Roboto+Condensed:wght@400;700&family=Open+Sans:wght@400;600&display=swap">
<style>
:root{
  --purple:#6a0aa8;
  --purple-bright:#7d13c9;
  --purple-deep:#4e1a9e;
  --ink:#2b2b2b;
  --grey:#666;
  --light:#f3f3f3;
  --line:#dcdcdc;
  --white:#fff;
  --dark:#262626;
}
*{box-sizing:border-box;margin:0;padding:0}
html,body{width:1200px;height:2290px;overflow:hidden}
body{position:relative;background:var(--white);font-family:"Open Sans",Arial,sans-serif;color:var(--ink)}
.head-font{font-family:"Roboto Condensed","Arial Narrow",sans-serif}

.site-header{position:absolute;top:0;left:0;width:1200px;height:97px;background:var(--purple)}
.brand{position:absolute;left:96px;top:22px;font:700 42px "Roboto Condensed","Arial Narrow",sans-serif;color:var(--white);letter-spacing:.5px}
.main-nav{position:absolute;left:413px;top:40px;display:flex;gap:0}
.main-nav a{font:400 15px "Roboto Condensed","Arial Narrow",sans-serif;color:var(--white);text-decoration:none;margin-right:31px}
.header-social{position:absolute;left:1016px;top:42px;display:flex;gap:6px}
.header-social span{width:11px;height:11px;border-radius:50%;background:var(--white)}

.hero{position:absolute;top:97px;left:0;width:1200px;height:380px}
.hero-photo{position:absolute;inset:0;background:radial-gradient(ellipse at 60% 40%,#5a6650 0%,#2f3a2a 45%,#1c2119 100%)}
.hero-curve{position:absolute;left:0;bottom:0;width:1200px;height:80px}
.hero-title{position:absolute;top:135px;width:1200px;text-align:center;font:400 40px "Roboto Condensed","Arial Narrow",sans-serif;color:var(--white)}
.hero-text{position:absolute;top:195px;width:1200px;text-align:center;font:400 15px/26px "Roboto Condensed","Arial Narrow",sans-serif;color:var(--white)}
.btn-read{position:absolute;left:537px;top:263px;width:126px;height:34px;border-radius:17px;background:var(--purple-bright);color:var(--white);font:400 15px/34px "Roboto Condensed","Arial Narrow",sans-serif;text-align:center}

.section-title{position:absolute;top:535px;width:1200px;text-align:center;font:400 35px "Roboto Condensed","Arial Narrow",sans-serif;color:var(--ink)}
.title-rule{position:absolute;top:592px;left:575px;width:50px;height:2px;background:var(--purple-bright)}

.book-card{position:absolute;width:234px;height:324px;background:var(--white);box-shadow:0 1px 5px rgba(0,0,0,.3)}
.book-cover{height:210px}
.book-genre{margin-top:15px;text-align:center;font:400 16px "Open Sans",Arial,sans-serif;color:#333;letter-spacing:.3px}
.book-blurb{margin:6px auto 0;width:190px;text-align:center;font:400 11px/17px "Open Sans",Arial,sans-serif;color:var(--grey)}
.book-rating{margin-top:4px;text-align:center;font-size:14px;color:var(--purple);letter-spacing:2px}

.newsletter-band{position:absolute;top:1448px;left:0;width:1200px;height:493px;background:linear-gradient(160deg,#5d2bd0 0%,#7a22b8 45%,#8a1fb0 100%)}
.video-frame{position:absolute;left:99px;top:95px;width:463px;height:298px;border:4px solid #e6e6e6;background:linear-gradient(135deg,#2a2e4a,#4a5070 50%,#222638)}
.video-frame .play{position:absolute;left:203px;top:125px;width:46px;height:46px;border-radius:50%;background:var(--purple-bright)}
.video-frame .play svg{position:absolute;left:16px;top:13px}
.video-controls{position:absolute;left:26px;right:26px;bottom:22px;height:8px}
.newsletter{position:absolute;left:617px;top:110px;width:390px}
.newsletter h2{font:700 31px "Roboto Condensed","Arial Narrow",sans-serif;color:var(--white)}
.newsletter p{margin-top:8px;font:600 11px/19px "Open Sans",Arial,sans-serif;color:var(--white)}
.field{margin-top:12px;height:40px;background:var(--white);font:400 11px/40px "Open Sans",Arial,sans-serif;color:#444;text-align:center}
.field:first-of-type{margin-top:14px}
.btn-subscribe{margin-top:12px;height:42px;background:var(--dark);color:var(--white);font:400 17px/42px "Roboto Condensed","Arial Narrow",sans-serif;text-align:center}

.site-footer{position:absolute;top:1941px;left:0;width:1200px;height:289px;background:var(--light)}
.footer-brand{position:absolute;left:96px;top:53px;font:700 38px "Roboto Condensed","Arial Narrow",sans-serif;color:var(--purple-bright)}
.footer-about{position:absolute;left:96px;top:112px;width:310px;font:400 11px/21px "Open Sans",Arial,sans-serif;color:#444}
.footer-col h3{font:400 18px "Roboto Condensed","Arial Narrow",sans-serif;color:var(--ink);margin-bottom:18px}
.footer-col{position:absolute;top:50px}
.contact-item{display:flex;gap:12px;font:400 12px/20px "Open Sans",Arial,sans-serif;color:#444;margin-bottom:10px}
.contact-item svg{flex:none;margin-top:3px}
.links li{list-style:none;font:400 11px/20.5px "Open Sans",Arial,sans-serif;color:#444;padding-left:16px;position:relative}
.links li::before{content:"";position:absolute;left:2px;top:7px;border-left:5px solid #444;border-top:3px solid transparent;border-bottom:3px solid transparent}
.social li{list-style:none;display:flex;align-items:center;gap:10px;font:400 14px "Open Sans",Arial,sans-serif;color:#444;margin-bottom:8px}
.social li span{width:26px;height:26px;border-radius:50%;border:1.5px solid #666}
.copyright{position:absolute;top:2230px;left:0;width:1200px;height:60px;border-top:1px solid var(--line);background:var(--white);text-align:center;font:400 11px/60px "Open Sans",Arial,sans-serif;color:#444}
</style>
</head>
<body>

<header class="site-header">
  <div class="brand">LARK WHITBY</div>
  <nav class="main-nav">
    <a>HOME</a><a>BOOKS</a><a>BLOG</a><a>RESOURCES</a><a>OTHER WORKS</a><a>STORE</a><a>CONTACT US</a>
  </nav>
  <div class="header-social" aria-label="Social links"><span></span><span></span><span></span><span></span><span></span></div>
</header>

<section class="hero">
  <div class="hero-photo" role="img" aria-label="Dark forest with a large tree trunk"></div>
  <svg class="hero-curve" viewBox="0 0 1200 80" preserveAspectRatio="none">
    <path d="M0 20 Q600 95 1200 0 L1200 80 L0 80 Z" fill="#7d13c9"/>
    <path d="M0 28 Q600 100 1200 10 L1200 80 L0 80 Z" fill="#fff"/>
  </svg>
  <h1 class="hero-title">OUR BOOKS</h1>
  <p class="hero-text">I AM AN AUTHOR AND WRITE MILD SCIFI / SECRET AGENT /<br>THRILLER / CONSPIRACY NOVELS</p>
  <div class="btn-read">READ MORE</div>
</section>

<h2 class="section-title">LATEST BOOK</h2>
<div class="title-rule"></div>

<article class="book-card" style="left:97px;top:643px"><div class="book-cover" role="img" aria-label="Cover: woman's portrait with white feathers" style="background:linear-gradient(90deg,#c8ccd2,#6a7380 55%,#2a3038)"></div><h3 class="book-genre">CONSPIRACY NOVELS</h3><p class="book-blurb">Sed ut perspiciatis unde omnis iste natus error sit voluptatem</p><div class="book-rating">★★★★☆</div></article>
<article class="book-card" style="left:355px;top:643px"><div class="book-cover" role="img" aria-label="Cover: agent in trench coat with a pistol" style="background:linear-gradient(160deg,#8a8780,#4b4843 60%,#2a2826)"></div><h3 class="book-genre">SECRET AGENT</h3><p class="book-blurb">Sed ut perspiciatis unde omnis iste natus error sit voluptatem</p><div class="book-rating">★★★★☆</div></article>
<article class="book-card" style="left:612px;top:643px"><div class="book-cover" role="img" aria-label="Cover: figure with a lantern on a shore at dusk" style="background:linear-gradient(180deg,#5f9aa3,#86a8ac 50%,#2a3336)"></div><h3 class="book-genre">CONSPIRACY NOVELS</h3><p class="book-blurb">Sed ut perspiciatis unde omnis iste natus error sit voluptatem</p><div class="book-rating">★★★★☆</div></article>
<article class="book-card" style="left:868px;top:643px"><div class="book-cover" role="img" aria-label="Cover: figure before a ruined archway" style="background:linear-gradient(180deg,#b3a692,#7d705e 60%,#3e362c)"></div><h3 class="book-genre">THRILLER</h3><p class="book-blurb">Sed ut perspiciatis unde omnis iste natus error sit voluptatem</p><div class="book-rating">★★★★☆</div></article>

<article class="book-card" style="left:97px;top:1020px"><div class="book-cover" role="img" aria-label="Cover: woman running through a forest" style="background:linear-gradient(160deg,#8ea06a,#4b5d38 55%,#2b3422)"></div><h3 class="book-genre">CONSPIRACY NOVELS</h3><p class="book-blurb">Sed ut perspiciatis unde omnis iste natus error sit voluptatem</p><div class="book-rating">★★★★☆</div></article>
<article class="book-card" style="left:355px;top:1020px"><div class="book-cover" role="img" aria-label="Cover: man in a suit holding a knife" style="background:linear-gradient(90deg,#2a2522,#6a5240 50%,#2a2522)"></div><h3 class="book-genre">SECRET AGENT</h3><p class="book-blurb">Sed ut perspiciatis unde omnis iste natus error sit voluptatem</p><div class="book-rating">★★★★☆</div></article>
<article class="book-card" style="left:612px;top:1020px"><div class="book-cover" role="img" aria-label="Cover: man running up a stairway" style="background:linear-gradient(180deg,#c4c9cc,#8a9094 55%,#3e4245)"></div><h3 class="book-genre">CONSPIRACY NOVELS</h3><p class="book-blurb">Sed ut perspiciatis unde omnis iste natus error sit voluptatem</p><div class="book-rating">★★★★☆</div></article>
<article class="book-card" style="left:868px;top:1020px"><div class="book-cover" role="img" aria-label="Cover: abandoned house under a stormy sky" style="background:linear-gradient(180deg,#3f5468,#6a7a88 50%,#2a343e)"></div><h3 class="book-genre">THRILLER</h3><p class="book-blurb">Sed ut perspiciatis unde omnis iste natus error sit voluptatem</p><div class="book-rating">★★★★☆</div></article>

<section class="newsletter-band">
  <div class="video-frame" role="img" aria-label="Book trailer video: woman reading a glowing book in a library">
    <div class="play"><svg width="16" height="20" viewBox="0 0 16 20"><path d="M0 0 L16 10 L0 20 Z" fill="#fff"/></svg></div>
    <svg class="video-controls" viewBox="0 0 403 8" preserveAspectRatio="none">
      <rect x="0" y="2" width="303" height="4" fill="#555"/>
      <rect x="0" y="2" width="134" height="4" fill="#c0201f"/>
      <rect x="320" y="1" width="30" height="6" fill="#c0201f"/>
      <rect x="360" y="1" width="14" height="6" fill="#c0201f"/>
      <rect x="388" y="1" width="8" height="6" fill="#ccc"/>
    </svg>
  </div>
  <div class="newsletter">
    <h2>SIGN UP FOR OUR NEWSLETTER</h2>
    <p>Sed ut perspiciatis unde omnis iste natus error sit voluptatem accusantium doloremque laudantium, totam rem aperiam, eaque ipsa quae ab illo inventore veritatis et quasi architecto beatae vitae dicta sunt explicabo</p>
    <div class="field">Enter Name</div>
    <div class="field">Enter Email</div>
    <div class="btn-subscribe">SUBSCRIBE</div>
  </div>
</section>

<footer class="site-footer">
  <div class="footer-brand">LARK WHITBY</div>
  <p class="footer-about">Sed ut perspiciatis unde omnis iste natus error sit voluptatem accusantium doloremque lauantium, totam rem aperiam, eaque ipsa quae ab illo inventore veritatis et quasi architecto beatae vitae dicta sunt explicabo</p>

  <div class="footer-col" style="left:473px">
    <h3>CONTACT US</h3>
    <div class="contact-item"><svg width="12" height="15" viewBox="0 0 12 15"><path d="M6 0a6 6 0 0 0-6 6c0 4 6 9 6 9s6-5 6-9a6 6 0 0 0-6-6zm0 8.5A2.5 2.5 0 1 1 6 3.5a2.5 2.5 0 0 1 0 5z" fill="#555"/></svg><span style="font-size:11px">Lark Whitby<br>Harrow Lane 14, 40217 Westfield</span></div>
    <div class="contact-item"><svg width="13" height="13" viewBox="0 0 13 13"><path d="M3 0l2 3-1.5 1.5a8 8 0 0 0 5 5L10 8l3 2-1.5 3C5 13 0 8 0 1.5z" fill="#555"/></svg><span>Phone: +49 555 01 23 456</span></div>
    <div class="contact-item"><svg width="12" height="9" viewBox="0 0 12 9"><rect width="12" height="9" fill="#555"/><path d="M0 0l6 5 6-5" stroke="#f3f3f3" fill="none"/></svg><span>info@larkwhitby.com</span></div>
  </div>

  <div class="footer-col" style="left:788px">
    <h3>QUICK LINKS</h3>
    <ul class="links"><li>Home</li><li>About the book</li><li>Blog</li><li>Resources</li><li>Blog</li><li>store</li><li>Contact Us</li></ul>
  </div>

  <div class="footer-col" style="left:998px">
    <h3>SOCIAL</h3>
    <ul class="social"><li><span></span>Pagebook</li><li><span></span>Chirper</li><li><span></span>Snapgram</li><li><span></span>Pinboard</li><li><span></span>clipvane</li></ul>
  </div>
</footer>

<div class="copyright">©2017 Lark Whitby, All Rights Reserved.</div>

</body>
</html>
```